SaaS Early tech startup business card design

Unique design for experience ecommerce platform company. the business cards will be used by executive members. conformance with color code is required.

```html
<!DOCTYPE html>
<html lang="en">
<head>
<meta charset="utf-8">
<title>Novaro business card</title>
<link href="https://fonts.googleapis.com/css2?family=Montserrat:wght@400;500;700;800&display=swap" rel="stylesheet">
<style>
  :root {
    --page: #e6e8ec;
    --card-white: #ffffff;
    --navy: #1e1f36;
    --deep-blue: #1b6a9a;
    --mid-blue: #1a8fa8;
    --teal: #13b9a0;
    --soft-teal: #4cc4a8;
    --ink: #2a2a2e;
    --ink-soft: #45464c;
  }
  * { margin: 0; padding: 0; box-sizing: border-box; }
  html, body {
    width: 1200px; height: 900px; overflow: hidden;
    background: var(--page);
    font-family: "Montserrat", sans-serif;
  }
  .sheet {
    width: 1200px; height: 900px;
    display: flex; flex-direction: column;
    align-items: center; justify-content: center; gap: 40px;
  }
  .card {
    width: 620px; height: 379px;
    position: relative; overflow: hidden;
    box-shadow: 0 10px 28px rgba(20, 22, 40, 0.18);
  }
  /* front */
  .card-front { background: var(--card-white); }
  .card-front .brand-band {
    position: absolute; left: 0; right: 0; bottom: 0; height: 9px;
    background: linear-gradient(90deg, var(--deep-blue), var(--mid-blue) 45%, var(--teal) 80%, var(--soft-teal));
  }
  .card-front .wordmark {
    position: absolute; left: 52px; top: 132px;
    font-weight: 800; font-size: 62px; letter-spacing: -2px;
    color: var(--mid-blue); line-height: 1;
  }
  .card-front .divider {
    position: absolute; left: 300px; top: 96px;
    width: 1.5px; height: 190px; background: var(--teal);
  }
  .contact {
    position: absolute; left: 328px; top: 104px; right: 24px;
    color: var(--ink-soft);
  }
  .contact .person {
    font-weight: 700; font-size: 19px; letter-spacing: 2.5px;
    text-transform: uppercase; color: var(--ink);
  }
  .contact .role { font-size: 13px; margin-top: 2px; }
  .contact .address { font-size: 13px; line-height: 1.4; margin-top: 14px; }
  .contact .lines { list-style: none; margin-top: 14px; font-size: 13px; line-height: 1.6; }
  .contact .lines li { display: flex; align-items: center; gap: 8px; }
  .contact .lines svg { width: 13px; height: 13px; flex: none; }
  /* back */
  .card-back {
    background: var(--navy);
    display: flex; align-items: center; justify-content: center;
  }
  .card-back .wordmark {
    font-weight: 800; font-size: 118px; letter-spacing: -4px;
    color: var(--mid-blue); line-height: 1;
  }
</style>
</head>
<body>
<main class="sheet">
  <section class="card card-front" aria-label="Business card front">
    <div class="wordmark">novaro</div>
    <div class="divider"></div>
    <div class="contact">
      <p class="person">Elias Brandt</p>
      <p class="role">Managing Director</p>
      <p class="address">Larch Street, Westfield<br>Harwood Park, 2417</p>
      <ul class="lines">
        <li>
          <svg viewBox="0 0 16 16" aria-hidden="true"><path fill="#1b6a9a" d="M3.6 1.5l2.2 2.6-1.3 1.6c.9 2 2.7 3.8 4.7 4.7l1.6-1.3 2.6 2.2-1.2 2.2C6.8 14.6 1.4 9.2 1.5 3z"/></svg>
          02 5550 1482
        </li>
        <li>
          <svg viewBox="0 0 16 16" aria-hidden="true"><rect x="4" y="1" width="8" height="14" rx="1.5" fill="none" stroke="#1b6a9a" stroke-width="1.6"/><circle cx="8" cy="12.3" r="0.9" fill="#1b6a9a"/></svg>
          0400 555 827
        </li>
        <li>
          <svg viewBox="0 0 16 16" aria-hidden="true"><rect x="1.5" y="3.5" width="13" height="9" rx="1" fill="none" stroke="#1b6a9a" stroke-width="1.6"/><path d="M2 4l6 5 6-5" fill="none" stroke="#1b6a9a" stroke-width="1.4"/></svg>
          hello@novaro.io
        </li>
        <li>
          <svg viewBox="0 0 16 16" aria-hidden="true"><circle cx="8" cy="8" r="6.3" fill="none" stroke="#1b6a9a" stroke-width="1.5"/><ellipse cx="8" cy="8" rx="2.6" ry="6.3" fill="none" stroke="#1b6a9a" stroke-width="1.2"/><path d="M1.8 8h12.4" stroke="#1b6a9a" stroke-width="1.2"/></svg>
          www.novaro.io
        </li>
      </ul>
    </div>
    <div class="brand-band"></div>
  </section>

  <section class="card card-back" aria-label="Business card back">
    <div class="wordmark">novaro</div>
  </section>
</main>
</body>
</html>
```